New Fun, Positive, energised looking Business Card Needed for High Achiever Coach

I am looking for a two sided full colour business card. I am self employed and have recently re branded my 1-2-1 work re-vitalising high achievers. My target client base for these cards is therefore high achievers - usually aged 40 -55, they are often entrepreneurs, CEO or work in banking and finance and 2/3 are male. I work with them on 90 day or 6 month coaching programs to help them live their success in a healthier, more sustainable and fulfiiled way. They pay for this privately so though they are corporate types the cards need not look 'corporate'. I want to portray the idea of transformation, vitality and re-connecting.
You can get a feel for the look I like on my new website: morvenlisk.co.uk
I want to use this logo with strapline (Re-Vitalising High Achievers) (I purchased off Logoharbor) and font/ colours (the turquoise and green).
Details to include on the card:
www.morvenlisk.co.uk
+44 7915 302618
morven@morvenlisk.co.uk
skype: morvenlisk
I'd also like to include:
Do you struggle to switch off? Want to be healthier and feel fitter? Want closer relationships? More clarity over the direction you are headed? I can help you do these things using integrated mind-body techniques. Visit morvenlisk.co.uk TODAY to apply for a FREE Breakthrough session.
BUT if that is too much text for a card I am open to advice/ammendments.
Updates
Thanks for your design - I am considering them. PLease change the wording to :

```html
<!DOCTYPE html>
<html lang="en">
<head>
<meta charset="utf-8">
<title>Morven Lisk – Business Card</title>
<link rel="stylesheet" href="https://fonts.googleapis.com/css2?family=Open+Sans:wght@400;600;700&display=swap">
<style>
  :root {
    --turquoise: #0aa3c6;
    --turquoise-dark: #0891b2;
    --leaf-green: #5cb85c;
    --ink: #2f3337;
    --rule: #b9bcc0;
    --paper: #ffffff;
    --backdrop: #e9eaec;
  }
  * { box-sizing: border-box; margin: 0; padding: 0; }
  html, body {
    width: 1200px; height: 987px; overflow: hidden;
    background: var(--backdrop);
    font-family: "Open Sans", Arial, sans-serif;
  }
  .sheet {
    width: 1200px; height: 987px;
    display: flex; flex-direction: column;
    align-items: center; justify-content: center; gap: 24px;
  }
  .card {
    position: relative;
    width: 800px; height: 457px;
    border-radius: 28px; overflow: hidden;
  }
  /* Front */
  .card-front { background: var(--paper); }
  .card-front .wave { position: absolute; inset: 0; }
  .brand {
    position: absolute; left: 50px; top: 110px; width: 270px;
    display: flex; flex-direction: column; align-items: center; gap: 12px;
  }
  .brand-dot {
    width: 64px; height: 64px; border-radius: 50%;
    background: var(--leaf-green);
  }
  .brand-name {
    font-size: 40px; font-weight: 700; color: var(--turquoise);
    line-height: 1;
  }
  .brand-strapline {
    font-size: 15px; font-weight: 400; color: var(--turquoise);
  }
  .divider {
    position: absolute; left: 345px; top: 90px;
    width: 2px; height: 200px;
    background: linear-gradient(var(--paper), var(--rule) 40%, var(--rule) 60%, var(--paper));
  }
  .contact-list {
    position: absolute; left: 380px; top: 110px;
    list-style: none; display: flex; flex-direction: column; gap: 22px;
  }
  .contact-item {
    display: flex; align-items: center; gap: 14px;
    font-size: 27px; color: var(--ink); line-height: 1;
  }
  .contact-icon { width: 24px; height: 24px; flex: none; }
  .site-url {
    position: absolute; left: 0; right: 230px; bottom: 28px;
    text-align: center;
    font-size: 30px; font-weight: 600; letter-spacing: 3px;
    color: var(--paper);
  }
  /* Back */
  .card-back {
    background: var(--turquoise);
    display: flex; flex-direction: column; justify-content: center; align-items: center;
    text-align: center; color: var(--paper);
    padding: 0 40px;
  }
  .pitch { font-size: 27px; line-height: 1.3; }
  .pitch + .pitch { margin-top: 14px; }
  .pitch strong { font-weight: 700; }
</style>
</head>
<body>
<main class="sheet">
  <section class="card card-front" aria-label="Card front">
    <svg class="wave" viewBox="0 0 800 457" preserveAspectRatio="none" aria-hidden="true">
      <path d="M0,270 C120,330 300,365 480,395 C600,415 680,435 720,457 L0,457 Z" fill="var(--turquoise)"/>
      <path d="M70,298 C260,352 470,372 610,405 C680,422 730,440 752,457" fill="none" stroke="var(--leaf-green)" stroke-width="5"/>
    </svg>
    <div class="brand">
      <span class="brand-dot"></span>
      <span class="brand-name">Morven Lisk</span>
      <span class="brand-strapline">Re-Vitalising High Achievers</span>
    </div>
    <div class="divider"></div>
    <ul class="contact-list">
      <li class="contact-item">
        <svg class="contact-icon" viewBox="0 0 24 24" aria-hidden="true">
          <circle cx="12" cy="12" r="11" fill="none" stroke="var(--turquoise)" stroke-width="2"/>
          <path d="M8 6.5c-1 1-1 2.6 0 4.5 1.3 2.5 3.4 4.6 5.6 5.8 1.7.9 3.2.8 4-.2l-2.1-2.2-1.6 1c-1.3-.7-2.6-2-3.3-3.3l1-1.6L9.4 6.3Z" fill="var(--turquoise)"/>
        </svg>
        <span>+44 7915 302618</span>
      </li>
      <li class="contact-item">
        <svg class="contact-icon" viewBox="0 0 24 24" aria-hidden="true">
          <rect x="2" y="5" width="20" height="14" rx="2" fill="var(--turquoise)"/>
          <path d="M3 6.5 12 13l9-6.5" fill="none" stroke="var(--paper)" stroke-width="1.8"/>
        </svg>
        <span>morven@morvenlisk.co.uk</span>
      </li>
      <li class="contact-item">
        <svg class="contact-icon" viewBox="0 0 24 24" aria-hidden="true">
          <rect x="2" y="2" width="20" height="20" rx="4" fill="var(--turquoise)"/>
        </svg>
        <span>morvenlisk</span>
      </li>
    </ul>
    <p class="site-url">www.morvenlisk.co.uk</p>
  </section>

  <section class="card card-back" aria-label="Card back">
    <p class="pitch">Do you struggle to switch off?<br>
      Want to be healthier and feel fitter?<br>
      Want closer relationships?<br>
      More clarity over the direction you are headed?<br>
      I can help you do these things using integrated<br>
      mind-body techniques.</p>
    <p class="pitch">Visit <strong>morvenlisk.co.uk</strong> TODAY to apply for a<br>
      FREE Breakthrough session.</p>
  </section>
</main>
</body>
</html>
```